Business Card Design (NEW FILES)

ATTENTION: New vector files are available. Please update your design to reflect/use the new (better resolution) logo images.

Seeking a unique and professional business card design for a commercial drone photography/videography business. The layout should feature
the logo (attached) and include the following information:
Owen Tarrick
614-502-7738
www.skylarkreelworks.example
NRD Certified Remote Pilot

Owen Tarrick

```html
<!DOCTYPE html>
<html lang="en">
<head>
<meta charset="utf-8">
<title>Skylark Reelworks – Business Card</title>
<link rel="stylesheet" href="https://fonts.googleapis.com/css2?family=Open+Sans:wght@400;600;800&display=swap">
<style>
  :root {
    --backdrop: #232323;
    --card-orange: #ec8b55;
    --orange-deep: #d9743e;
    --navy: #181c4e;
    --navy-band: #1c2157;
    --navy-shade: #141842;
    --white: #ffffff;
  }
  * { margin: 0; padding: 0; box-sizing: border-box; }
  html, body { width: 1200px; height: 780px; overflow: hidden; }
  body {
    background: var(--backdrop);
    font-family: "Open Sans", Arial, sans-serif;
    position: relative;
  }
  .card {
    position: absolute;
    top: 110px;
    width: 320px;
    height: 560px;
    border-radius: 22px;
    overflow: hidden;
    box-shadow: 0 18px 40px rgba(0,0,0,0.55);
  }
  /* Front */
  .card-front {
    left: 230px;
    background: var(--card-orange);
    display: flex;
    align-items: center;
    justify-content: center;
  }
  .front-brand {
    display: flex;
    align-items: center;
    gap: 14px;
    transform: rotate(-90deg);
    white-space: nowrap;
  }
  .front-brand .brand-dot {
    width: 26px; height: 26px;
    border-radius: 50%;
    background: var(--orange-deep);
  }
  .front-brand .brand-name {
    font-weight: 600;
    font-size: 40px;
    letter-spacing: 2px;
    color: var(--orange-deep);
    text-transform: uppercase;
  }
  /* Back */
  .card-back {
    left: 650px;
    background: var(--navy);
    color: var(--white);
  }
  .back-bands {
    position: absolute;
    inset: 0;
  }
  .back-brand {
    position: absolute;
    top: 62px;
    left: 0; right: 0;
    display: flex;
    justify-content: center;
    align-items: center;
    gap: 10px;
  }
  .back-brand .brand-dot {
    width: 16px; height: 16px;
    border-radius: 50%;
    background: var(--card-orange);
  }
  .back-brand .brand-name {
    font-weight: 600;
    font-size: 22px;
    letter-spacing: 1.5px;
    text-transform: uppercase;
    color: var(--white);
  }
  .person {
    position: absolute;
    top: 196px;
    left: 0; right: 0;
    text-align: center;
  }
  .person-name {
    font-size: 30px;
    font-weight: 800;
    line-height: 1.1;
  }
  .person-name .first { color: var(--card-orange); }
  .person-name .last { color: var(--white); }
  .person-role {
    font-size: 14px;
    font-weight: 600;
    margin-top: 2px;
  }
  .contact-icons {
    display: flex;
    justify-content: center;
    gap: 10px;
    margin-top: 14px;
  }
  .contact-icons .icon {
    width: 26px; height: 26px;
    border-radius: 50%;
    background: var(--card-orange);
    display: flex;
    align-items: center;
    justify-content: center;
  }
  .contact-list {
    list-style: none;
    margin-top: 12px;
    font-size: 13px;
    font-weight: 600;
    line-height: 1.55;
  }
  .credentials {
    position: absolute;
    bottom: 44px;
    left: 0; right: 0;
    text-align: center;
    font-size: 14px;
    font-weight: 600;
    line-height: 1.45;
  }
</style>
</head>
<body>
  <section class="card card-front" aria-label="Card front">
    <div class="front-brand">
      <span class="brand-dot"></span>
      <span class="brand-name">Skylark Reelworks</span>
    </div>
  </section>

  <section class="card card-back" aria-label="Card back">
    <svg class="back-bands" viewBox="0 0 320 560" preserveAspectRatio="none" aria-hidden="true">
      <path d="M0 560 L0 380 Q170 420 320 300 L320 560 Z" fill="var(--navy-shade)"/>
      <path d="M0 560 L0 400 Q200 430 320 340 L320 560 Z" fill="var(--navy-band)"/>
      <path d="M60 560 Q200 470 320 440 L320 560 Z" fill="var(--navy-shade)" opacity="0.7"/>
    </svg>

    <div class="back-brand">
      <span class="brand-dot"></span>
      <span class="brand-name">Skylark Reelworks</span>
    </div>

    <div class="person">
      <h1 class="person-name"><span class="first">Owen</span> <span class="last">Tarrick</span></h1>
      <p class="person-role">Owner</p>
      <div class="contact-icons">
        <span class="icon" aria-label="Phone">
          <svg width="14" height="14" viewBox="0 0 24 24"><path d="M6.6 10.8a15 15 0 0 0 6.6 6.6l2.2-2.2a1 1 0 0 1 1-.25 11.4 11.4 0 0 0 3.6.57 1 1 0 0 1 1 1V20a1 1 0 0 1-1 1A17 17 0 0 1 3 4a1 1 0 0 1 1-1h3.5a1 1 0 0 1 1 1c0 1.25.2 2.45.57 3.6a1 1 0 0 1-.25 1Z" fill="#fff"/></svg>
        </span>
        <span class="icon" aria-label="Email">
          <svg width="14" height="14" viewBox="0 0 24 24"><rect x="3" y="6" width="18" height="12" rx="1.5" fill="none" stroke="#fff" stroke-width="2"/><path d="M3 7l9 6 9-6" fill="none" stroke="#fff" stroke-width="2"/></svg>
        </span>
        <span class="icon" aria-label="Website">
          <svg width="14" height="14" viewBox="0 0 24 24"><circle cx="12" cy="12" r="9" fill="none" stroke="#fff" stroke-width="2"/><path d="M3 12h18M12 3c3 3 3 15 0 18M12 3c-3 3-3 15 0 18" fill="none" stroke="#fff" stroke-width="1.6"/></svg>
        </span>
      </div>
      <ul class="contact-list">
        <li>614-502-7738</li>
        <li>www.skylarkreelworks.example</li>
        <li>info@skylarkreelworks.example</li>
      </ul>
    </div>

    <p class="credentials">NRD Certified Remote Pilot<br>Fully Insured</p>
  </section>
</body>
</html>
```